Small Business Directory Site Requires a Professional Responsive Web Design

Small Business Directory and Coupon Site - we require a complete website design for a brand new responsive & mobile friendly website. We already have a coder who will professional code our website in Magento.

All PSD pages need to be professionally designed then uploaded into a sharedrive (i.e. like filecrate). Additionally, as I cannot pre-empt everything, please note that we may require a little more assistance once the files have been transferred (for example, in www.brightlane-listings.example if you hover your mouse on the search box you will see a pop up box. We want one of these too and I think that means there may be extra design work here)

We have some draft page sketches have been created (there are some minor changes we want to the sketches provided though); however, we require an excellent designer to add the creative touches to it to make it look professionally created. All artwork/font must be legal.

-------------------------
We like the look of the www.brightlane-listings.example and www. marlowfolio.example

For the headers, please consider a font similar to RNS camellia. We likes this style, but it is too thin for the headers...so we need a variation like this one. For the copy/general text font, something basic that marries well with the headers.

---------------------

Please be sure to also read the brief we wrote for the coder as this will help with better understanding our design requirements.

In total I believe we have about 50 pages. This includes all the little pages and most of the pop up boxes (but not the little help key boxes). For example, pages include...

1. Login (this is where customers log in and can edit, manage their profiles. This means that there are backend membership pages)
2. Mini Services (same look and feel as the business coupons)
3. Resource Centre
4. Join (this is where customers learn about the packages available to submit a directory listing, if they ‘buy’ a package (i.e. free, $25 or $150 package) then they can create their own directory listing)
5. Search the directory (customer can view all the categories and also search the directory)
6. Create a directory listing (this is where customers learn about the packages available to submit a directory listing, if they ‘buy’ a package (i.e. free, $25 or $150 package) then they can create their own directory listing)
7. Quote finder (also know as Get a Quote)
8. Coupons (customer go to the business coupon page and can view all current coupons/submit a coupon)
9. Submit a coupon (form)
10.Advertise with us (form)
11. Join the forum
12.Submit an article or video (form)
13. Affiliates (listing of affiliates we currently have)
14. Become an affiliate (form)
15. Case studies (customer can view the case studies we have in the resource centre)
16. Help Guides (customer can view the help guides we have in the resource centre)
17. About Us
18 .Contact Us (form)
19. Terms & Condition
20. Privacy Policy
21. Supporting City Councils
22. Site Map
23. Forgot password / login details
24. Homepage
25. If we hover over a few areas (i.e. search box, location field) it pops up with more information.
etc etc etc. . . there are more pages.

Please see our filecrate link for the draft mock up pages that I have created so far.

https://www.cloudtrunk.example/sh/qk72pmw4rtz8nd/KLMvbTq2fWndxPzs8Yh4ecRQu

We are in a rush! We'd like to get the majority of the artwork completed by the end of the month. Minor fixes/tweaks can occur thereafter.

Target Market(s)

Small Businesses (employees 0 - 50) located throughout Australia

Industry/Entity Type

Business

Font styles to use
Sans Serif

Requirements
Must have
• Professional. Artwork must be legal (cannot be cut and paste or taken off other websites, must be legally purchased and used).Must look contemporary, fresh, modern.

Absolutely must be a responsive site!
Nice to have
• original work, original photos, original art.

like modern, fresh photos that demonstrate innovation, growth, small business, Australian scenery, stability, goals/passion.
Should not have
• cut and paste graphics, illegal graphics, not purchased graphics.

```html
<!DOCTYPE html>
<html lang="en">
<head>
<meta charset="utf-8">
<title>BizHelp Link – Small Business Directory</title>
<link href="https://fonts.googleapis.com/css2?family=Quicksand:wght@400;500;600;700&display=swap" rel="stylesheet">
<style>
:root{
  --orange:#f7901e;
  --orange-dark:#e8780c;
  --ink:#333333;
  --muted:#666666;
  --line:#e3e3e3;
  --bar:#1e1e1e;
  --footer:#000000;
  --footer-base:#2a2a2a;
  --white:#ffffff;
}
*{box-sizing:border-box;margin:0;padding:0}
html,body{width:778px;height:1200px;overflow:hidden;background:var(--white)}
body{position:relative;font-family:'Quicksand',sans-serif;color:var(--ink)}
.abs{position:absolute}

/* header */
.site-header{left:0;top:0;width:778px;height:70px;background:var(--white)}
.brand{left:82px;top:22px;display:flex;align-items:center;gap:8px}
.brand-mark{width:24px;height:24px;background:var(--orange)}
.brand-name{font-size:17px;font-weight:600;color:var(--ink)}
.main-nav{right:89px;top:30px;display:flex;font-size:9.5px;font-weight:500}
.main-nav span{padding:0 7px;border-left:1px solid #ccc}
.main-nav span:first-child{border-left:none}

/* hero */
.hero{left:0;top:70px;width:778px;height:303px;
  background:linear-gradient(160deg,#2c3e5c 0%,#4a5f84 30%,#8a6a5a 55%,#c98a3f 72%,#3a4c6e 100%)}
.hero-title{left:84px;top:88px;font-size:25px;font-weight:500;color:var(--white)}
.hero-sub{left:84px;top:119px;font-size:13px;font-weight:500;color:var(--white)}
.search-box{left:84px;top:146px;width:364px;height:42px;background:var(--orange);padding:9px 11px;display:flex;gap:5px}
.search-field{height:23px;background:var(--white);font-size:7px;color:#888;padding:7px 8px}
.search-btn{width:25px;height:23px;background:#111;display:flex;align-items:center;justify-content:center}
.join-btn{width:58px;height:23px;background:#111;color:var(--white);font-size:10px;font-weight:700;display:flex;align-items:center;justify-content:center}
.promo{left:514px;top:44px;width:181px;height:206px;background:rgba(90,90,90,.75)}
.promo-title{position:absolute;left:0;top:16px;width:100%;text-align:center;color:var(--white);font-size:13px;font-weight:500;line-height:18px}
.promo-visual{position:absolute;left:38px;top:58px;width:105px;height:72px;background:linear-gradient(135deg,#e6e6e6,#c9a94a);border:4px solid #333}
.promo-base{position:absolute;left:32px;top:130px;width:117px;height:4px;background:#bbb}
.promo-label{position:absolute;left:16px;top:143px;font-size:7px;color:var(--orange);font-weight:600}
.promo-text{position:absolute;left:16px;top:153px;font-size:6.5px;color:#eee}
.promo-price{position:absolute;left:16px;top:174px;font-size:12px;color:var(--white)}
.promo-price small{font-size:7px}
.promo-btn{position:absolute;left:93px;top:174px;width:64px;height:17px;background:var(--orange);color:var(--white);font-size:6.5px;font-weight:600;display:flex;align-items:center;justify-content:center}
.promo-arrow{position:absolute;top:92px}
.dots{left:369px;display:flex;gap:4px}
.dots i{width:8px;height:8px;border-radius:50%;background:var(--white);display:block}

/* categories */
.cat-bar{left:0;top:373px;width:778px;height:27px;background:var(--bar)}
.cat-list{left:82px;top:373px;height:27px;display:flex;font-size:8.1px;font-weight:500;color:var(--white)}
.cat-list span{padding:0 5.5px;border-left:1px solid #555;display:flex;align-items:center}
.cat-list span:first-child{border-left:none}
.cat-list .cat-all{background:var(--orange);border-left:none;padding:0 8px}

/* community */
.section-title{width:778px;left:0;text-align:center;font-weight:500;color:var(--ink)}
.community-title{top:421px;font-size:19.5px}
.col{top:466px;width:200px;text-align:center}
.col-title{color:var(--orange);font-size:12.5px;font-weight:500;line-height:18px;height:40px;display:flex;align-items:center;justify-content:center}
.col-media{margin:6px auto 0;width:186px;height:104px;border:1px solid #ccc}
.col-text{margin-top:11px;font-size:7.3px;line-height:13.2px;color:var(--muted)}
.btn{display:inline-flex;align-items:center;justify-content:center;height:21px;padding:0 14px;background:var(--orange);color:var(--white);font-size:7.5px;font-weight:600;border-radius:2px;box-shadow:0 1px 0 var(--orange-dark)}
.affiliate-box{margin:8px auto 0;width:169px;height:97px;border:1px solid #ddd;display:flex;align-items:center;justify-content:center;gap:6px}
.affiliate-name{font-size:18px;font-weight:700;color:#1d2a55}
.affiliate-mark{width:18px;height:18px;border-radius:50%;background:#1d8fd0}
.divider{left:82px;top:746px;width:614px;height:1px;background:var(--line)}

/* coupons */
.coupon-title-main{top:764px;font-size:14.5px}
.coupon{top:798px;width:129px;height:122px;border:1px solid #ddd;text-align:center}
.coupon-art{margin:18px auto 0;width:76px;height:42px}
.coupon-name{margin-top:14px;color:var(--orange);font-size:9.5px;font-weight:500}
.coupon-desc{margin-top:2px;font-size:7px;color:var(--muted)}
.coupon-price{margin-top:5px;font-size:11.5px;font-weight:500;color:#222}

/* partners */
.partners{left:0;top:944px;width:778px;height:48px;background:#f3f3f3;display:flex;align-items:center;justify-content:center;gap:90px;font-size:19px;font-weight:700;color:#9a9a9a}

/* footer */
.site-footer{left:0;top:992px;width:778px;height:168px;background:var(--footer)}
.f-col{top:1019px}
.f-col h4{font-size:9.5px;font-weight:600;color:var(--orange);margin-bottom:7px}
.f-col li{list-style:none;font-size:7.5px;color:var(--white);line-height:14px;font-weight:500}
.social{display:flex;gap:6px;margin-top:2px}
.social i{display:block;width:17px;height:17px;background:#8a8a8a;border-radius:2px}
.subscribe{margin-top:13px;display:inline-flex;align-items:center;height:19px;padding:0 5px;background:var(--orange);font-size:7.5px;font-weight:500;color:#111}
.footer-base{left:0;top:1160px;width:778px;height:40px;background:var(--footer-base)}
.copyright{left:90px;top:1177px;font-size:7.5px;color:#888}
</style>
</head>
<body>

<header class="abs site-header">
  <div class="abs brand"><span class="brand-mark"></span><span class="brand-name">BizHelp Link</span></div>
  <nav class="abs main-nav">
    <span>Login</span><span>Join</span><span>Coupons</span><span>Mini Service</span><span>Get a Quote</span><span>Advertise</span><span>Resource Centre</span>
  </nav>
</header>

<section class="abs hero" role="img" aria-label="City skyline at dusk with glowing highways">
  <h1 class="abs hero-title">It's a Brand New Day.</h1>
  <p class="abs hero-sub">Do More of What Your Love</p>
  <div class="abs search-box">
    <div class="search-field" style="width:135px">What are you looking for?</div>
    <div class="search-field" style="width:115px">Where?</div>
    <div class="search-btn"><svg width="13" height="13" viewBox="0 0 13 13"><circle cx="5.5" cy="5.5" r="4" fill="none" stroke="#fff" stroke-width="1.6"/><line x1="8.5" y1="8.5" x2="12" y2="12" stroke="#fff" stroke-width="1.8"/></svg></div>
    <div class="join-btn">Join Us</div>
  </div>
  <aside class="abs promo">
    <div class="promo-title">Create a Business<br>Coupons today</div>
    <svg class="promo-arrow" style="left:13px" width="10" height="18" viewBox="0 0 10 18"><polyline points="8,1 2,9 8,17" fill="none" stroke="#fff" stroke-width="1.5"/></svg>
    <svg class="promo-arrow" style="left:158px" width="10" height="18" viewBox="0 0 10 18"><polyline points="2,1 8,9 2,17" fill="none" stroke="#fff" stroke-width="1.5"/></svg>
    <div class="promo-visual" role="img" aria-label="Laptop showing a gold gift voucher"></div>
    <div class="promo-base"></div>
    <div class="promo-label">3 CATEGORY LISTING</div>
    <div class="promo-text">Lorem ipsum dolor sit amet consectetuer adip</div>
    <div class="promo-price">A $25/<small>YEAR</small></div>
    <div class="promo-btn">CLICK HERE</div>
  </aside>
  <div class="abs dots" style="top:288px"><i></i><i></i><i></i><i></i></div>
</section>

<div class="abs cat-bar"></div>
<nav class="abs cat-list">
  <span>Banking, Finance &amp; Insurance</span><span>Marketing, Design, Photography, Video &amp; Print</span><span>Coaching &amp; Training</span><span>Technology</span><span>Legal</span><span>Administration</span><span class="cat-all">View All Category</span>
</nav>

<h2 class="abs section-title community-title">Get Real Support from Our Community</h2>

<div class="abs col" style="left:89px">
  <h3 class="col-title">How Did You Sort<br>Your Business?</h3>
  <div class="col-media" style="background:linear-gradient(135deg,#e9edf1,#c9d3dc)" role="img" aria-label="Hands writing beside a tablet and glasses on a desk"></div>
  <p class="col-text" style="padding:0 14px">Text: Learn from Dana Holloway, a real small business owner. How she started her business and what are the valuable resources for her right now.</p>
  <div style="margin-top:16px"><span class="btn">CASE STUDY</span></div>
</div>

<div class="abs col" style="left:300px">
  <h3 class="col-title">Why Go with<br>BizHelp Link?</h3>
  <div class="col-media" style="width:182px;background:linear-gradient(135deg,#b9c6d3,#3e5677);position:relative" role="img" aria-label="Two colleagues discussing work at a laptop, video">
    <svg style="position:absolute;left:77px;top:38px" width="28" height="28" viewBox="0 0 28 28"><circle cx="14" cy="14" r="14" fill="#fff"/><polygon points="11,8 20,14 11,20" fill="#111"/></svg>
  </div>
  <p class="col-text" style="margin-top:7px">What small business owner can't relate to theongoing task of attracting new customers? Struggling with cash flow? Or how about not having enough time in the day? It's obvious that small businesses suffer from a lack of support. And that's where we come in</p>
  <div style="margin-top:9px"><span class="btn">WHITEBOARD VIDEO</span></div>
</div>

<div class="abs col" style="left:501px">
  <h3 class="col-title">Become an Affiliate</h3>
  <div class="affiliate-box"><span class="affiliate-mark"></span><span class="affiliate-name">Harbor Cover</span></div>
  <p class="col-text" style="margin-top:13px">If you have a network of small businesses, let us help to create additional value for your members and make money for your network. Talk to us today about how we can help.</p>
</div>

<div class="abs divider"></div>

<h2 class="abs section-title coupon-title-main">Featured Business Coupons</h2>

<div class="abs coupon" style="left:115px">
  <div class="coupon-art" style="background:#cfe0c8;border:2px solid #5c7d55" role="img" aria-label="Green banknote style coupon with logo space"></div>
  <div class="coupon-name">Coupon Tittle</div><div class="coupon-desc">Lorem ipsum dolor sit amet</div><div class="coupon-price">$3,000</div>
</div>
<div class="abs coupon" style="left:254px">
  <div class="coupon-art" style="background:#f4efe2;border:2px solid #3c7a45" role="img" aria-label="Breakfast in bed voucher with green frame"></div>
  <div class="coupon-name">Coupon Tittle</div><div class="coupon-desc">Lorem ipsum dolor sit amet</div><div class="coupon-price">$3,000</div>
</div>
<div class="abs coupon" style="left:392px">
  <div class="coupon-art" style="background:linear-gradient(#6cc3c8,#e8dcb8)" role="img" aria-label="Cupcake shop twenty percent off voucher"></div>
  <div class="coupon-name">Coupon Tittle</div><div class="coupon-desc">Lorem ipsum dolor sit amet</div><div class="coupon-price">$3,000</div>
</div>
<div class="abs coupon" style="left:531px">
  <div class="coupon-art" style="background:linear-gradient(90deg,#fff 55%,#e9eef0)" role="img" aria-label="Ten dollars off shopping voucher"></div>
  <div class="coupon-name">Coupon Tittle</div><div class="coupon-desc">Lorem ipsum dolor sit amet</div><div class="coupon-price">$3,000</div>
</div>

<div class="abs partners"><span>Tallwood</span><span>Gridmark</span><span>Norvane</span></div>

<footer class="abs site-footer"></footer>
<div class="abs f-col" style="left:84px"><h4>SITE DIRECTORY</h4><ul><li>Search the Directory</li><li>Create a Directory Listing</li><li>Quote Finder</li><li>Coupons</li><li>Submit A Coupon</li><li>Advertise with us</li></ul></div>
<div class="abs f-col" style="left:203px"><h4>SITE DIRECTORY</h4><ul><li>Join the Forum</li><li>Submit an Article or Video</li><li>Affiliates</li><li>Become an Affiliate</li><li>Case Studies</li><li>Help Guides</li></ul></div>
<div class="abs f-col" style="left:325px"><h4>POPULAR CATEGORIES</h4><ul><li>Etiam est nunc</li><li>Venenatis tristique</li><li>Emperdiet ac nisl</li><li>Cum sociis natoque</li><li>Penatibus et magnis</li></ul></div>
<div class="abs f-col" style="left:458px"><h4>ABOUT</h4><ul><li>About Us</li><li>Contact Us</li><li>Term &amp; Conditions</li><li>Privacy Policy</li><li>Supporting City Councils</li><li>Site Map</li></ul></div>
<div class="abs f-col" style="left:570px"><h4>FOLLOW US</h4>
  <div class="social"><i aria-label="Video channel"></i><i aria-label="Social page"></i><i aria-label="Microblog"></i><i aria-label="Professional network"></i></div>
  <div class="subscribe">Subscribe to our Coupon Deals</div>
</div>
<div class="abs footer-base"></div>
<p class="abs copyright">© 2014 Company Name  All right reserved  Term of Use</p>

</body>
</html>
```